KBT Business Cards

We require business cards for our business. We would like a matte black back to the card, with our logo centred in the middle. The front side of the card is open to design.

Target Market(s)

Clients looking for legal services (professional)

Industry/Entity Type

Legal

Contact Information for Business Card

Doran Kelbrath
Partner
Mobile: 0461 738 524
Email: doran@kbtlaw.co
Website: www.kbtlaw.co
Level 3, 118 Wendmore Street
Sydney NSW 2000

Font styles to use
Other font styles liked:
• Avenir

Colors
f04a50
ffffff
1b1b1b

Requirements
Must have
• Black back with logo included in the centre of the card.
• Our font is Avenir.

```html
<!DOCTYPE html>
<html lang="en">
<head>
<meta charset="utf-8">
<title>KBT Business Cards</title>
<link rel="stylesheet" href="https://fonts.googleapis.com/css2?family=Nunito+Sans:wght@400;600;800&display=swap">
<style>
  :root {
    --red: #c8184a;
    --red-bright: #f04a50;
    --white: #ffffff;
    --ink: #1b1b1b;
    --black: #0d0d0d;
    --stage: #2a2a2a;
    --muted: #e6e6e6;
  }
  * { box-sizing: border-box; margin: 0; padding: 0; }
  html, body { width: 1200px; height: 960px; overflow: hidden; }
  body {
    background: var(--stage);
    font-family: "Nunito Sans", "Avenir", sans-serif;
    position: relative;
  }
  .card {
    position: absolute;
    left: 300px;
    width: 600px;
    height: 343px;
    overflow: hidden;
    border-radius: 4px;
    box-shadow: 0 10px 30px rgba(0,0,0,.35);
  }
  .card--back { top: 100px; background: var(--ink); }
  .card--front { top: 517px; background: var(--white); }

  .brand {
    display: flex;
    align-items: center;
    gap: 14px;
  }
  .brand__mark {
    width: 46px; height: 46px;
    background: var(--red);
    flex: none;
  }
  .brand__name {
    font-weight: 800;
    font-size: 26px;
    line-height: 1.02;
    text-transform: uppercase;
    letter-spacing: .2px;
  }
  .card--back .brand {
    position: absolute;
    left: 50%; top: 118px;
    transform: translateX(-50%);
  }
  .card--back .brand__name { color: var(--white); }
  .back__web {
    position: absolute;
    left: 0; right: 0; top: 262px;
    text-align: center;
    color: var(--white);
    font-size: 14px;
    letter-spacing: 4px;
  }
  .back__web .accent { color: var(--red-bright); font-weight: 600; }

  .front__shape { position: absolute; inset: 0; }
  .card--front .brand {
    position: absolute;
    left: 36px; top: 110px;
  }
  .card--front .brand__name { color: var(--ink); font-size: 22px; }

  .contact {
    position: absolute;
    right: 30px; top: 96px;
    text-align: right;
    color: var(--white);
  }
  .contact__name {
    font-weight: 800;
    font-size: 18px;
    letter-spacing: .5px;
    text-transform: uppercase;
  }
  .contact__role {
    font-size: 13px;
    letter-spacing: 1px;
    text-transform: uppercase;
    margin-bottom: 14px;
  }
  .contact__list { list-style: none; }
  .contact__item {
    display: flex;
    justify-content: flex-end;
    align-items: center;
    gap: 8px;
    font-size: 13px;
    line-height: 22px;
  }
  .contact__icon { width: 14px; height: 14px; flex: none; }
  .contact__address {
    font-style: normal;
    font-size: 13px;
    line-height: 19px;
    margin-top: 6px;
    padding-right: 22px;
  }
</style>
</head>
<body>

<section class="card card--back" aria-label="Card back">
  <div class="brand">
    <span class="brand__mark"></span>
    <span class="brand__name">Kelbrath<br>Bowe<br>Tarrant</span>
  </div>
  <p class="back__web">www.<span class="accent">kbtlaw</span>.co</p>
</section>

<section class="card card--front" aria-label="Card front">
  <svg class="front__shape" viewBox="0 0 600 343" width="600" height="343" aria-hidden="true">
    <path d="M362 0 H600 V343 H236 C334 262 384 122 362 0 Z" fill="var(--black)"/>
    <path d="M352 0 C378 122 328 262 226 343 H236 C334 262 384 122 362 0 Z" fill="var(--red)"/>
  </svg>

  <div class="brand">
    <span class="brand__mark"></span>
    <span class="brand__name">Kelbrath<br>Bowe<br>Tarrant</span>
  </div>

  <div class="contact">
    <p class="contact__name">Doran Kelbrath</p>
    <p class="contact__role">Partner</p>
    <ul class="contact__list">
      <li class="contact__item">0461 738 524
        <svg class="contact__icon" viewBox="0 0 14 14" aria-hidden="true"><rect x="3.5" y="1" width="7" height="12" rx="1.5" fill="none" stroke="currentColor" stroke-width="1.3"/><circle cx="7" cy="10.8" r=".8" fill="currentColor"/></svg>
      </li>
      <li class="contact__item">doran@kbtlaw.co
        <svg class="contact__icon" viewBox="0 0 14 14" aria-hidden="true"><rect x="1" y="3" width="12" height="8" fill="none" stroke="currentColor" stroke-width="1.3"/><path d="M1 3 L7 8 L13 3" fill="none" stroke="currentColor" stroke-width="1.3"/></svg>
      </li>
      <li class="contact__item">www.kbtlaw.co
        <svg class="contact__icon" viewBox="0 0 14 14" aria-hidden="true"><circle cx="7" cy="7" r="5.8" fill="none" stroke="currentColor" stroke-width="1.2"/><ellipse cx="7" cy="7" rx="2.5" ry="5.8" fill="none" stroke="currentColor" stroke-width="1.1"/><path d="M1.2 7 H12.8" stroke="currentColor" stroke-width="1.1"/></svg>
      </li>
    </ul>
    <address class="contact__address">Level 3, 118 Wendmore Street<br>Sydney NSW 2000</address>
  </div>
</section>

</body>
</html>
```